Landing page design for my current website

I need a landing page designed for my Wordpress website. My website is Velmorquay.com, and I need a page that will serve as a landing page for online ads I run. Please follow the color scheme of the current website

This web page will be targeted towards real estate owners who are looking for a property manager. Above the fold needs to have a CTA form headlined with "As a Rental Property Owner, I Want More Protection, Less Stress, and Drama-Free Living"

A few highlights that can be listed beyond the CTA and fold

- Comprehensive Property Management
Full-service management covering tenant placement, leasing, maintenance, and inspections.

Maximized Rental Income
Proven strategies to optimize rental rates and minimize vacancies, ensuring higher ROI.

Stress-Free Management
We handle all tenant interactions, maintenance requests, and property issues, so you don't have to.

Experienced Team
Over a decade of experience in managing single-family homes, small multifamily units, and apartment complexes.

Advanced Technology
Utilize cutting-edge property management software for efficient communication, rent collection, and maintenance tracking.

Tenant Screening and Placement
Thorough background checks and tenant screening processes to ensure reliable and responsible tenants.

Regular Property Inspections
Routine inspections to maintain property condition and address issues before they become costly problems.

Legal Compliance
Expertise in local and federal rental laws to keep your properties compliant and avoid legal hassles.

Transparent Reporting
Detailed monthly reports and financial statements to keep you informed about your property's performance.

Personalized Service
Tailored management plans to meet the unique needs of your properties and investment goals.
Effective Tenant Conflict Resolution
Skilled in handling challenging tenant situations, ensuring conflicts are resolved quickly and professionally to maintain a peaceful living environment and protect your investment.

```html
<!DOCTYPE html>
<html lang="en">
<head>
<meta charset="utf-8">
<title>Velmorquay Realty – Property Management</title>
<link href="https://fonts.googleapis.com/css2?family=Montserrat:wght@400;500;600;700&display=swap" rel="stylesheet">
<style>
:root{
  --navy:#0f3d73;
  --navy-dark:#123a66;
  --title:#173f73;
  --text:#4a4f57;
  --muted:#6b7078;
  --line:#d9dde3;
  --white:#ffffff;
  --page:#ffffff;
}
*{box-sizing:border-box;margin:0;padding:0}
html,body{width:1200px;height:5128px;overflow:hidden}
body{font-family:"Montserrat",sans-serif;background:var(--page);color:var(--text);position:relative}

.topbar{height:50px;display:flex;align-items:center;justify-content:space-between;padding:0 110px;font-size:14px;color:#3b3f45;background:var(--white)}
.topbar .contact{display:flex;align-items:center;gap:18px}
.topbar .sep{width:1px;height:26px;background:#9aa0a8}
.topbar svg{vertical-align:-2px;margin-right:6px}

.hero{position:relative;height:578px;overflow:hidden}
.hero-photo{position:absolute;inset:0;background:linear-gradient(180deg,#dde6ef 0%,#eef1f4 40%,#e4ddd0 75%,#cfc6b6 100%)}
.header{position:absolute;top:0;left:0;right:0;height:90px;display:flex;align-items:center;justify-content:space-between;padding:0 110px}
.brand{display:flex;align-items:center;gap:10px;font-weight:700;font-size:21px;color:var(--navy);letter-spacing:.5px}
.brand .mark{width:44px;height:44px;border:3px solid var(--navy);border-radius:50%}
.nav{display:flex;gap:30px;font-size:16px;color:#2d3238}
.nav a{color:inherit;text-decoration:none;padding-bottom:6px}
.nav a.active{color:var(--navy);font-weight:600;border-bottom:2px solid var(--navy)}

.hero-copy{position:absolute;left:110px;top:185px;width:480px}
.hero-copy .kicker{font-size:27px;font-weight:600;color:#25282c}
.hero-copy h1{font-size:42px;font-weight:700;color:var(--navy);margin-top:6px}
.hero-copy p{font-size:14.5px;line-height:24px;color:#2b2e33;margin-top:20px}

.lead-form{position:absolute;left:704px;top:136px;width:384px;height:374px;background:var(--white);border-radius:30px;padding:30px 26px 0;text-align:center}
.lead-form h2{font-size:19px;font-weight:700;color:var(--navy);letter-spacing:.3px}
.lead-form .sub{font-size:13px;line-height:19px;color:#3c4046;margin-top:6px}
.lead-form .rule{width:180px;height:1px;background:var(--navy);margin:12px auto 22px}
.lead-form .field{height:40px;border:1px solid var(--line);border-radius:4px;text-align:left;padding-left:14px;font-size:14px;color:#8a8f96;line-height:38px;margin:0 0 16px 0}
.lead-form .submit{height:40px;background:var(--navy);color:var(--white);border-radius:4px;font-size:15px;font-weight:600;line-height:40px;margin-top:2px}
.lead-form .submit svg{vertical-align:-2px;margin-left:6px}

.features{padding:90px 0 24px}
.feature{position:relative;height:386px}
.feature .frame{position:absolute;top:22px;width:284px;height:294px;background:var(--navy)}
.feature .photo{position:absolute;top:0;width:477px;height:294px}
.feature .card{position:absolute;top:56px;width:540px;min-height:150px;background:var(--white);padding:36px 40px 0 20px}
.feature h3{font-size:21px;font-weight:500;color:var(--title)}
.feature p{font-size:14.5px;line-height:22px;color:var(--muted);margin-top:14px;text-align:justify}
.feature.left .frame{left:118px}
.feature.left .photo{left:137px}
.feature.left .card{left:562px}
.feature.right .frame{left:804px}
.feature.right .photo{left:592px}
.feature.right .card{left:100px;padding-left:36px;width:540px}

.footer{position:absolute;left:0;right:0;top:4988px;height:140px;background:var(--navy-dark);color:var(--white)}
.footer .links{display:flex;justify-content:center;gap:28px;font-size:16px;padding-top:34px}
.footer .divider{position:absolute;left:110px;right:110px;top:90px;height:1px;background:rgba(255,255,255,.35)}
.footer .copy{position:absolute;left:110px;top:110px;font-size:14px}
.footer .social{position:absolute;right:110px;top:104px;display:flex;gap:8px}
.footer .social span{width:28px;height:28px;border:1.5px solid rgba(255,255,255,.8);border-radius:50%}
</style>
</head>
<body>

<div class="topbar">
  <div><svg width="12" height="14" viewBox="0 0 12 14"><path d="M6 0a5 5 0 0 0-5 5c0 4 5 9 5 9s5-5 5-9a5 5 0 0 0-5-5zm0 7a2 2 0 1 1 0-4 2 2 0 0 1 0 4z" fill="#333"/></svg>Sed ut perspiciatis unde omnis</div>
  <div class="contact">
    <span><svg width="13" height="13" viewBox="0 0 13 13"><path d="M3 0l2 3-1.5 1.5a8 8 0 0 0 5 5L10 8l3 2-1.5 2.5C6 13 0 7 .5 1.5z" fill="#333"/></svg>+1 555 0100 2040</span>
    <span class="sep"></span>
    <span><svg width="14" height="11" viewBox="0 0 14 11"><rect width="14" height="11" rx="1" fill="#333"/><path d="M1 1l6 5 6-5" stroke="#fff" fill="none"/></svg>info@velmorquay.com</span>
  </div>
</div>

<section class="hero">
  <div class="hero-photo" role="img" aria-label="Modern white apartment buildings with balconies under a pale sky"></div>
  <header class="header">
    <div class="brand"><span class="mark"></span>VELMORQUAY REALTY</div>
    <nav class="nav">
      <a href="#" class="active">Home</a>
      <a href="#">Real Estate</a>
      <a href="#">Property Single</a>
      <a href="#">Blog</a>
      <a href="#">Contact</a>
    </nav>
  </header>
  <div class="hero-copy">
    <div class="kicker">Discover Your Perfect</div>
    <h1>Rental Home Today</h1>
    <p>Lorem ipsum dolor sit amet, consectetur adipiscing elit, sed do eiusmod tempor incididunt ut</p>
  </div>
  <form class="lead-form">
    <h2>AS A RENTAL PROPERTY OWNER,</h2>
    <div class="sub">I Want More Protection, Less Stress, and<br>Drama-Free Living</div>
    <div class="rule"></div>
    <div class="field">Name</div>
    <div class="field">E-Mail</div>
    <div class="field">Address</div>
    <div class="submit">SUBMIT<svg width="14" height="14" viewBox="0 0 14 14"><path d="M0 6L14 0 10 14 7 8z" fill="#fff"/></svg></div>
  </form>
</section>

<main class="features">
  <article class="feature left">
    <div class="frame"></div>
    <div class="photo" role="img" aria-label="Suburban street of family houses with green lawns" style="background:linear-gradient(180deg,#bcd3ea 0%,#9fb0a8 55%,#6f8f4d 100%)"></div>
    <div class="card"><h3>Comprehensive Property Management</h3><p>Full-service management covering tenant placement, leasing, maintenance, and inspections.</p></div>
  </article>
  <article class="feature right">
    <div class="frame"></div>
    <div class="photo" role="img" aria-label="Model house beside stacks of coins and a calculator" style="background:linear-gradient(90deg,#1c1a18 0%,#8a6a45 45%,#e4d6bf 100%)"></div>
    <div class="card"><h3>Maximized Rental Income</h3><p>Proven strategies to optimize rental rates and minimize vacancies, ensuring higher ROI.</p></div>
  </article>
  <article class="feature left">
    <div class="frame"></div>
    <div class="photo" role="img" aria-label="Agent greeting a couple at a home" style="background:linear-gradient(90deg,#9ec3e4 0%,#d8d4cc 50%,#8fb4d8 100%)"></div>
    <div class="card"><h3>Stress-Free Management</h3><p>We handle all tenant interactions, maintenance requests, and property issues, so you don't have to.</p></div>
  </article>
  <article class="feature right">
    <div class="frame"></div>
    <div class="photo" role="img" aria-label="Business team standing in a bright office with a blue wall" style="background:linear-gradient(90deg,#e9ebee 0%,#1d4fb0 45%,#2759c0 70%,#e2e4e8 100%)"></div>
    <div class="card"><h3>Experienced Team</h3><p>Over a decade of experience in managing single-family homes, small multifamily units, and apartment complexes.</p></div>
  </article>
  <article class="feature left">
    <div class="frame"></div>
    <div class="photo" role="img" aria-label="Model house on a desk with digital network lines" style="background:linear-gradient(135deg,#0c1a2e 0%,#2b4266 50%,#c9b89a 100%)"></div>
    <div class="card"><h3>Advanced Technology</h3><p>Utilize cutting-edge property management software for efficient communication, rent collection, and maintenance tracking.</p></div>
  </article>
  <article class="feature right">
    <div class="frame"></div>
    <div class="photo" role="img" aria-label="Hands holding a tablet showing a virtual home tour" style="background:linear-gradient(90deg,#d9d2c6 0%,#a88a62 45%,#2a2d33 100%)"></div>
    <div class="card"><h3>Tenant Screening and Placement</h3><p>Thorough background checks and tenant screening processes to ensure reliable and responsible tenants.</p></div>
  </article>
  <article class="feature left">
    <div class="frame"></div>
    <div class="photo" role="img" aria-label="Inspector in hard hat and safety vest at a building site" style="background:linear-gradient(90deg,#cfcac2 0%,#c8d04a 40%,#8a8e94 100%)"></div>
    <div class="card"><h3>Regular Property Inspections</h3><p>Routine inspections to maintain property condition and address issues before they become costly problems.</p></div>
  </article>
  <article class="feature right">
    <div class="frame"></div>
    <div class="photo" role="img" aria-label="Hand signing a contract with a pen" style="background:linear-gradient(180deg,#6e6e70 0%,#a7a8ab 45%,#eeeeef 100%)"></div>
    <div class="card"><h3>Legal Compliance</h3><p>Expertise in local and federal rental laws to keep your properties compliant and avoid legal hassles.</p></div>
  </article>
  <article class="feature left">
    <div class="frame"></div>
    <div class="photo" role="img" aria-label="Tablet with financial charts on a desk of reports" style="background:linear-gradient(135deg,#f2f3f5 0%,#b9cfe6 50%,#3f5a80 100%)"></div>
    <div class="card"><h3>Transparent Reporting</h3><p>Detailed monthly reports and financial statements to keep you informed about your property's performance.</p></div>
  </article>
  <article class="feature right">
    <div class="frame"></div>
    <div class="photo" role="img" aria-label="Growing stacks of coins topped by small houses" style="background:linear-gradient(180deg,#b8c8dc 0%,#dfe6ee 55%,#c9a24e 100%)"></div>
    <div class="card"><h3>Personalized Service</h3><p>Tailored management plans to meet the unique needs of your properties and investment goals.</p></div>
  </article>
  <article class="feature left">
    <div class="frame"></div>
    <div class="photo" role="img" aria-label="Red umbrella sheltering a small house" style="background:linear-gradient(180deg,#dfe8ef 0%,#c7d4de 50%,#7e8f9e 100%)"></div>
    <div class="card"><h3>Effective Tenant Conflict Resolution</h3><p>Skilled in handling challenging tenant situations, ensuring conflicts are resolved quickly and professionally to maintain a peaceful living environment and protect your investment.</p></div>
  </article>
</main>

<footer class="footer">
  <div class="links"><span>Home</span><span>Real Estate</span><span>Property Single</span><span>Blog</span><span>Contact</span></div>
  <div class="divider"></div>
  <div class="copy">Copyrights 2024 Velmorquay. All Rights Reserved.</div>
  <div class="social"><span></span><span></span><span></span><span></span><span></span></div>
</footer>

</body>
</html>
```